Business cards for Norwegian software consultancy business

We are in need of business cards for our Norwegian consultancy company.
“Valto Brindex AS” specializes in software development, architecture and agile methodology, providing mostly on-site services at customers.
The cards should reflect a certain level of business professionalism with an elegant touch, while paying tribute to our modern and technological heritage. Our logo should be featured, as well as room for basic information about the cardholder and legal information of the company (company name, address and VAT number).
We would like our cards to reflect that we are a modern consulting company. It should present a professional image that people will remember. The texture and color pallette should reflect our professionalism and reliability, so we prefer a light color pallette with colors such as gray, white, blue and black. The number of colors used should however not be overwhelming, with the text being distinct and readable.
We are open to untraditional layouts and playful designs as long as they communicate the intent stated above.
You could also take a look at our website http://www.brindex.no for input on our visual profile.
Our logo is attached in the form of vectors and rasterized PNG. Please comment if you would like the black-white and/or inverted versions as well.
Industry/Entity Type
Architecture
Contact Information for Business Card
Company information:
Valto Brindex AS
Kvernlia 14, 3170 Sem
482 71 519
info@brindex.no
www.brindex.no
Employee information:
Full name
Title
Email
Phone
Font styles to use
Look and feel

```html
<!DOCTYPE html>
<html lang="no">
<head>
<meta charset="utf-8">
<title>Valto Brindex AS – Business Card</title>
<link href="https://fonts.googleapis.com/css2?family=Lato:wght@400;700&display=swap" rel="stylesheet">
<style>
  :root {
    --page-bg: #d8d5d1;
    --card-top: #eceae7;
    --card-bottom: #dedbd7;
    --brand-blue: #5580ab;
    --brand-blue-deep: #45709b;
    --panel-dark: #1d1d1f;
    --ink: #262628;
    --cream: #e9dcc6;
    --cream-soft: #d9cbb3;
    --strip: #d3cfca;
  }
  * { margin: 0; padding: 0; box-sizing: border-box; }
  html, body {
    width: 1200px; height: 970px; overflow: hidden;
    background: var(--page-bg);
    font-family: "Lato", sans-serif;
  }
  .card {
    position: absolute; left: 50px; top: 180px;
    width: 1100px; height: 610px;
    background: linear-gradient(180deg, var(--card-top), var(--card-bottom));
    box-shadow: 0 18px 40px rgba(0,0,0,.18);
    overflow: hidden;
  }
  .brand {
    position: absolute; left: 0; right: 0; top: 0; height: 303px;
    display: flex; align-items: center; justify-content: center; gap: 26px;
  }
  .brand-square {
    width: 58px; height: 58px; background: var(--brand-blue);
  }
  .brand-name {
    font-weight: 400; font-size: 70px; letter-spacing: 4px;
    color: var(--ink); text-transform: uppercase;
  }
  .holder {
    position: absolute; left: 0; top: 303px; width: 547px; height: 248px;
    background: linear-gradient(180deg, var(--brand-blue), var(--brand-blue-deep));
    color: var(--cream);
    text-align: center;
  }
  .holder-notch {
    position: absolute; left: 262px; top: 0; width: 26px; height: 16px;
  }
  .holder-name { margin-top: 82px; font-size: 39px; font-weight: 400; }
  .holder-title { margin-top: 2px; font-size: 23px; letter-spacing: 1px; }
  .contact {
    position: absolute; left: 553px; top: 303px; width: 547px; height: 248px;
    background: var(--panel-dark);
    color: var(--cream);
  }
  .contact-pointer {
    position: absolute; left: 0; top: 105px; width: 24px; height: 36px;
  }
  .contact-list {
    list-style: none; position: absolute; left: 120px; top: 46px;
    font-size: 29px; line-height: 38px;
  }
  .contact-list li { display: flex; align-items: center; gap: 20px; }
  .contact-list svg { width: 24px; height: 24px; flex: none; }
  .legal {
    position: absolute; left: 0; right: 0; bottom: 0; height: 59px;
    background: var(--strip);
    display: flex; align-items: center; justify-content: center;
    font-size: 27px; color: var(--ink);
  }
  .legal .accent { color: var(--brand-blue); }
</style>
</head>
<body>
  <div class="card">
    <header class="brand">
      <span class="brand-square"></span>
      <span class="brand-name">Valto Brindex</span>
    </header>

    <section class="holder">
      <svg class="holder-notch" viewBox="0 0 26 16"><polygon points="0,0 26,0 13,16" fill="#e4e1dd"/></svg>
      <p class="holder-name">Eirik Solvang</p>
      <p class="holder-title">DIRECTOR</p>
    </section>

    <section class="contact">
      <svg class="contact-pointer" viewBox="0 0 24 36"><polygon points="0,0 24,18 0,36" fill="#e9dcc6"/></svg>
      <ul class="contact-list">
        <li>
          <svg viewBox="0 0 24 24" fill="none" stroke="#d9cbb3" stroke-width="2"><path d="M5 3l4 1 1 5-3 2a12 12 0 006 6l2-3 5 1 1 4c-1 2-3 3-5 2C9 19 5 15 3 8 2 6 3 4 5 3z"/></svg>
          482 71 519
        </li>
        <li>
          <svg viewBox="0 0 24 24" fill="none" stroke="#d9cbb3" stroke-width="2"><rect x="6" y="3" width="12" height="7"/><rect x="3" y="10" width="18" height="9"/><line x1="7" y1="15" x2="17" y2="15"/></svg>
          482 71 520
        </li>
        <li>
          <svg viewBox="0 0 24 24" fill="none" stroke="#d9cbb3" stroke-width="2"><rect x="3" y="5" width="18" height="14"/><polyline points="3,5 12,13 21,5"/></svg>
          esolvang@brindex.no
        </li>
        <li>
          <svg viewBox="0 0 24 24" fill="none" stroke="#d9cbb3" stroke-width="2"><circle cx="12" cy="12" r="9"/><ellipse cx="12" cy="12" rx="4" ry="9"/><line x1="3" y1="12" x2="21" y2="12"/></svg>
          www.brindex.no
        </li>
      </ul>
    </section>

    <footer class="legal">
      <span>Valto <span class="accent">Brindex AS</span>, Kvernlia 14, 3170 Sem</span>
    </footer>
  </div>
</body>
</html>
```